Redesign of business card for Cedar Ridge Mechanical

We are looking for a new design for our business cards for Cedar Ridge Mechanical. We are a plumbing & HVAC construction company, operating on the West Coast of Canada and USA. Logo attached.
Industry/Entity Type
Construction - Plumbing & HVAC
Contact Information for Business Card
Name, address, phone numbers, email, website address
Look and feel
Each slider illustrates characteristics of the customer's brand and the style your logo design should communicate.

```html
<!DOCTYPE html>
<html lang="en">
<head>
<meta charset="utf-8">
<title>Cedar Ridge Mechanical – Business Cards</title>
<link rel="stylesheet" href="https://fonts.googleapis.com/css2?family=Open+Sans:wght@400;700&family=Oswald:wght@400&display=swap">
<style>
  :root {
    --backdrop: #222222;
    --ink: #111111;
    --paper: #ffffff;
    --steel: #8a8c8e;
    --muted: #d9d9d9;
  }
  * { box-sizing: border-box; margin: 0; padding: 0; }
  html, body { width: 1200px; height: 780px; overflow: hidden; }
  body {
    background: var(--backdrop);
    display: flex;
    align-items: center;
    justify-content: center;
    gap: 40px;
    font-family: "Open Sans", Arial, sans-serif;
  }
  .card {
    position: relative;
    width: 520px;
    height: 300px;
    background: var(--paper);
    overflow: hidden;
    box-shadow: 0 12px 30px rgba(0,0,0,.45);
  }
  .card__wave { position: absolute; inset: 0; width: 100%; height: 100%; }
  .contact {
    position: absolute;
    left: 32px;
    top: 40px;
    color: var(--paper);
  }
  .contact__name {
    font-weight: 700;
    font-size: 17px;
    letter-spacing: .3px;
    text-transform: uppercase;
  }
  .contact__role { font-size: 11px; color: var(--muted); margin-top: 1px; }
  .contact__address { font-size: 11.5px; line-height: 1.45; margin-top: 14px; }
  .contact__list { list-style: none; margin-top: 14px; font-size: 11.5px; line-height: 1.7; }
  .contact__list li { display: flex; align-items: center; gap: 7px; }
  .contact__list svg { width: 10px; height: 10px; fill: var(--paper); }
  .wordmark {
    position: absolute;
    display: flex;
    align-items: center;
    gap: 12px;
    font-family: "Oswald", "Arial Narrow", sans-serif;
    font-weight: 400;
    text-transform: uppercase;
    color: var(--ink);
    letter-spacing: 1px;
  }
  .wordmark__square {
    background: var(--ink);
    flex: none;
  }
  .card--front .wordmark { left: 318px; top: 124px; font-size: 17px; line-height: 1.15; }
  .card--front .wordmark__square { width: 26px; height: 26px; }
  .card--back .wordmark {
    left: 0; right: 0; top: 0; bottom: 0;
    justify-content: center;
    font-size: 30px;
  }
  .card--back .wordmark__square { width: 34px; height: 34px; }
</style>
</head>
<body>

  <section class="card card--front" aria-label="Business card front">
    <svg class="card__wave" viewBox="0 0 520 300" preserveAspectRatio="none" aria-hidden="true">
      <path d="M0 0 H165 C250 0 235 300 395 300 H0 Z" fill="var(--steel)"/>
      <path d="M0 0 H152 C238 0 222 300 370 300 H0 Z" fill="var(--paper)"/>
      <path d="M0 0 H146 C230 0 212 300 355 300 H0 Z" fill="var(--ink)"/>
      <path d="M0 12 H140 C218 12 200 300 338 300" fill="none" stroke="var(--paper)" stroke-width="2"/>
    </svg>
    <div class="contact">
      <p class="contact__name">Daniel Hayes</p>
      <p class="contact__role">Managing Director</p>
      <p class="contact__address">Your address, City<br>State, Zip 1234</p>
      <ul class="contact__list">
        <li><svg viewBox="0 0 10 10"><path d="M2 0.5 L3.8 2.6 L2.9 3.6 C3.5 5 4.9 6.4 6.4 7.1 L7.4 6.2 L9.5 8 L8.3 9.5 C4.5 9.3 0.7 5.5 0.5 1.7 Z"/></svg>123 456 789</li>
        <li><svg viewBox="0 0 10 10"><path d="M0.5 2 H9.5 V8.5 H0.5 Z M1.2 2.6 L5 5.6 L8.8 2.6" stroke="var(--ink)" stroke-width=".8"/></svg>info@yourgmail.com</li>
        <li><svg viewBox="0 0 10 10"><circle cx="5" cy="5" r="4.5"/><path d="M0.5 5 H9.5 M5 0.5 C2.5 3 2.5 7 5 9.5 M5 0.5 C7.5 3 7.5 7 5 9.5" fill="none" stroke="var(--ink)" stroke-width=".7"/></svg>www.yourwebsite.com</li>
      </ul>
    </div>
    <div class="wordmark">
      <span class="wordmark__square"></span>
      <span>Cedar Ridge<br>Mechanical</span>
    </div>
  </section>

  <section class="card card--back" aria-label="Business card back">
    <div class="wordmark">
      <span class="wordmark__square"></span>
      <span>Cedar Ridge Mechanical</span>
    </div>
  </section>

</body>
</html>
```